Boutique custom software development company needs new business card

Our nearly 20 year old custom software development company would like to better include the fact that we are now providing Bitcoin services. These new services are B2B include education (how to acquire and securely hold Bitcoin) and integrating Bitcoin payments into existing ecommerce sites or other existing systems. Please keep the card clean and simple. Attached is our current design and some other files. vextorial.com

Target Market(s)

businesses owners interested in long term relationship

Industry/Entity Type

Custom software development and Bitcoin

Contact Information for Business Card

Dale Parker, dale@vextorial.com, vextorial.com, (888) 555-VXTRL

Font styles to use
Other font styles liked:
• monospace

Requirements
Must have
• double-sided
Nice to have
• clean and simple
Should not have
• physical address

```html
<!DOCTYPE html>
<html lang="en">
<head>
<meta charset="utf-8">
<title>Vextorial business card</title>
<link rel="stylesheet" href="https://fonts.googleapis.com/css2?family=Arimo:wght@400;700&family=Archivo+Black&display=swap">
<style>
  :root {
    --brand-blue: #3a6cb0;
    --brand-orange: #e8781f;
    --paper: #f7f7f5;
    --ink: #1c1c1c;
    --stage: #d9d9d6;
  }
  * { margin: 0; padding: 0; box-sizing: border-box; }
  html, body {
    width: 1200px;
    height: 912px;
    overflow: hidden;
    background: var(--stage);
    font-family: "Arimo", Arial, sans-serif;
  }
  .card {
    position: absolute;
    left: 250px;
    width: 700px;
    height: 400px;
    overflow: hidden;
    box-shadow: 0 6px 18px rgba(0,0,0,0.18);
  }
  .card-front { top: 36px; background: var(--brand-blue); }
  .card-back { top: 476px; background: var(--paper); }

  .front-shapes { position: absolute; inset: 0; }

  .front-url {
    position: absolute;
    right: 56px;
    top: 178px;
    font-family: "Arimo", Arial, sans-serif;
    font-weight: 700;
    font-size: 30px;
    letter-spacing: 1.5px;
    color: #ffffff;
  }
  .front-url .url-name { color: var(--brand-orange); }

  .brand {
    position: absolute;
    right: 48px;
    top: 44px;
    text-align: left;
  }
  .brand-name {
    font-family: "Arimo", Arial, sans-serif;
    font-weight: 700;
    font-size: 44px;
    letter-spacing: 1px;
    color: var(--brand-blue);
    line-height: 1;
  }
  .brand-tagline {
    margin-top: 4px;
    font-size: 15px;
    color: var(--brand-blue);
  }

  .person {
    position: absolute;
    left: 48px;
    bottom: 96px;
  }
  .person-name {
    font-family: "Archivo Black", "Arial Black", sans-serif;
    font-size: 38px;
    color: var(--brand-blue);
    line-height: 1.05;
  }
  .person-role {
    font-size: 22px;
    color: var(--brand-orange);
  }

  .contact {
    position: absolute;
    left: 48px;
    bottom: 44px;
    font-size: 17px;
    color: var(--ink);
    white-space: nowrap;
  }
  .contact-label {
    color: var(--brand-orange);
    font-weight: 700;
    margin-right: 4px;
  }
  .contact-sep { color: var(--ink); margin: 0 9px; }
</style>
</head>
<body>

  <section class="card card-front" aria-label="Card front">
    <svg class="front-shapes" viewBox="0 0 700 400" width="700" height="400" aria-hidden="true">
      <polygon points="0,230 220,400 0,400" fill="#f4f4f4"/>
      <polygon points="0,300 130,400 0,400" fill="var(--brand-orange)"/>
    </svg>
    <p class="front-url">www.<span class="url-name">vextorial</span>.com</p>
  </section>

  <section class="card card-back" aria-label="Card back">
    <div class="brand">
      <p class="brand-name">VEXTORIAL</p>
      <p class="brand-tagline">developer of custom applications</p>
    </div>

    <div class="person">
      <p class="person-name">Dale Parker</p>
      <p class="person-role">Bitcoin educator</p>
    </div>

    <p class="contact">
      <span class="contact-label">P :</span>(888) 555-VXTRL<span class="contact-sep">|</span><span class="contact-label">E :</span>dale@vextorial.com<span class="contact-sep">|</span><span class="contact-label">W :</span>www.vextorial.com
    </p>
  </section>

</body>
</html>
```